IT Company that provides secure IT solutions and services to our customers

We need business cards and a logo for a new IT Solutions company just created based in Kuala Lumpur, Malaysia. But will also be serving other countries in the region. We provide secure data, voice solutions on mobile platforms. Our first offering is encrypted voice and data solutions for IOS, Android, Windows and BlackBerry devices.

Target Market(s)

large organizations Govt, Police, Defence, Anti-corruption, Legal, highly regulated industries such as Health-care, Financial, Banking, Insurance,

Industry/Entity Type

Information Technology

Contact Information for Business Card

VelmoraNet (Logo - colour is ORVEX blue)Roshan Adeel Managing Director Kryption IT Sdn. Bhd.5th Floor, Block D, Wisma PLB,No.14 Jalan Seri Melor,50470, Kuala LumpurMalaysia

Font styles to use
Sans Serif

Colors
3176b5
ec1f27
fbed22

Requirements
Must have
• VelmoraNet all in Blue like ORVEX blue. A logo design perhaps a play of VN, K with a dangling T (colour can be any)
Nice to have
• I want a clean crisp card, not too busy, easy to read.

```html
<!DOCTYPE html>
<html lang="en">
<head>
<meta charset="utf-8">
<title>VelmoraNet Business Card</title>
<link href="https://fonts.googleapis.com/css2?family=Open+Sans:wght@400;600;700;800&display=swap" rel="stylesheet">
<style>
  :root {
    --brand-blue: #1f5fae;
    --brand-red: #d42a2c;
    --card-white: #ffffff;
    --card-black: #262626;
    --backdrop: #e9e6e1;
  }
  * { margin: 0; padding: 0; box-sizing: border-box; }
  html, body {
    width: 1200px; height: 900px; overflow: hidden;
    background: var(--backdrop);
    font-family: "Open Sans", Arial, sans-serif;
  }
  .sheet {
    width: 1200px; height: 900px;
    display: flex; flex-direction: column;
    align-items: center; justify-content: center; gap: 40px;
  }
  .card {
    position: relative;
    width: 700px; height: 400px;
    box-shadow: 0 6px 18px rgba(0,0,0,0.18);
    overflow: hidden;
  }
  .card-back {
    background: var(--card-black);
    display: flex; align-items: center; justify-content: center;
  }
  .card-front { background: var(--card-white); }

  .wordmark {
    font-weight: 800;
    font-size: 64px;
    letter-spacing: -1px;
    line-height: 1;
  }
  .card-back .wordmark { color: var(--card-white); }
  .card-front .wordmark {
    position: absolute; left: 330px; top: 170px;
    font-size: 52px; color: var(--brand-blue);
  }

  .corner-mark { position: absolute; left: 0; top: 0; }
  .person { position: absolute; left: 82px; top: 20px; }
  .person-name { font-size: 18px; font-weight: 700; color: var(--brand-blue); line-height: 1.2; }
  .person-name .surname { color: var(--brand-red); }
  .person-title { font-size: 13px; color: var(--brand-red); line-height: 1.2; }

  .company { position: absolute; left: 30px; top: 160px; }
  .company-name { font-size: 17px; font-weight: 700; color: var(--brand-blue); line-height: 1.25; }
  .company-address { font-size: 14.5px; color: var(--brand-red); line-height: 1.3; font-style: normal; }

  .bands { position: absolute; left: 0; bottom: 0; }
</style>
</head>
<body>
<main class="sheet">
  <section class="card card-back" aria-label="Card back">
    <span class="wordmark">VelmoraNet</span>
  </section>

  <section class="card card-front" aria-label="Card front">
    <svg class="corner-mark" width="70" height="60" viewBox="0 0 70 60">
      <polygon points="18,14 62,14 18,52" fill="var(--brand-blue)"/>
      <polygon points="66,16 66,52 24,52" fill="var(--brand-red)"/>
    </svg>

    <div class="person">
      <p class="person-name">Roshan <span class="surname">Adeel</span></p>
      <p class="person-title">Managing Director</p>
    </div>

    <div class="company">
      <p class="company-name">Velmora Net</p>
      <address class="company-address">
        Sdn. Bhd.5th Floor, Block D,<br>
        Wisma PLB,No.14 Jalan Seri Melor,<br>
        50470, Kuala Lumpur<br>
        Malaysia
      </address>
    </div>

    <span class="wordmark">VelmoraNet</span>

    <svg class="bands" width="700" height="80" viewBox="0 0 700 80">
      <polygon points="0,8 300,8 282,26 0,26" fill="var(--brand-blue)"/>
      <polygon points="300,30 700,30 700,80 258,80" fill="var(--brand-red)"/>
    </svg>
  </section>
</main>
</body>
</html>
```